Summit Builders Web Site / Business Cards

Construction Company that specializes in Water and Fire Damage, Residential ReModels, Landscaping and Building ADU (Accessory Dwelling Unit)

Growing and changing families often need additional space, and a remodeling project can often provide that. Adding a new area, or repurposing an existing one can satisfy this requirement.

Other times, homeowners want to update the look in their kitchen or bathroom with more than just a change of cabinetry or vanity doors and drawers. Whatever your needs are, Summit Builders has skilled workers who are bonded and insured, and ready to make your dreams and visions a reality.

Target Market(s)

Home Owners

Industry/Entity Type

Construction Company

Contact Information for Business Card

Center Logo with our information on the corners

Back side to be Logo Only
Contact Info
CSLB License # 2418596
info@summitbuildersca.example
www.summitbuildersca.example

Coding

Coded - Design and coding required

Number of Pages Required

5+ page

Font styles to use
Serif
Sans Serif

Requirements
Must have
• Using our Logo Colors
Home
About Us
Services
Projects / Portfolio
Contact Us
Nice to have
• Colors matching our Logo
Should not have
• Black because it doesnt match our logo

```html
<!DOCTYPE html>
<html lang="en">
<head>
<meta charset="utf-8">
<title>Summit Builders</title>
<link href="https://fonts.googleapis.com/css2?family=Poppins:wght@700;800&family=Nunito+Sans:wght@300;400;600;700&display=swap" rel="stylesheet">
<style>
:root{
  --orange:#f26a10;
  --navy:#143f72;
  --hero-top:#1c2f52;
  --hero-mid:#3b5680;
  --hero-low:#6f7a7c;
  --text:#2b2b2b;
  --muted:#555;
  --field:#f6f7f9;
  --footer:#434343;
  --white:#fff;
}
*{margin:0;padding:0;box-sizing:border-box}
html,body{width:1200px;height:3260px;overflow:hidden}
body{position:relative;font-family:"Nunito Sans",sans-serif;color:var(--text);background:var(--white)}
.abs{position:absolute}

/* hero */
.hero{left:0;top:0;width:1200px;height:642px;background:linear-gradient(175deg,var(--hero-top) 0%,var(--hero-mid) 45%,var(--hero-low) 80%,#8a8f6a 100%)}
.brand{display:flex;align-items:center;gap:9px;font-family:"Nunito Sans",sans-serif;font-weight:700;font-size:17px;line-height:19px;letter-spacing:1.5px;color:var(--white)}
.brand .mark{flex:none;width:14px;height:14px;background:var(--orange)}
.brand .words{display:flex;flex-direction:column}
.nav{top:42px;left:0;width:1200px;height:20px;font-size:14px;font-weight:600;color:var(--white);letter-spacing:.3px}
.nav a{position:absolute;color:var(--white);text-decoration:none}
.nav a.active{color:var(--orange)}
.nav a.active::after{content:"";position:absolute;left:0;right:0;top:26px;height:2px;background:var(--orange)}
.quote-btn{left:952px;top:33px;width:134px;height:34px;border:1.5px solid var(--orange);color:var(--white);font-size:14px;font-weight:600;display:flex;align-items:center;justify-content:center;letter-spacing:.3px}
.hero-title{top:248px;left:0;width:1200px;text-align:center;font-family:"Poppins",sans-serif;font-weight:800;font-size:64px;letter-spacing:4px;color:var(--white)}
.hero-sub{top:334px;left:0;width:1200px;text-align:center;font-size:23px;font-weight:300;color:var(--white)}
.side-social circle{fill:var(--orange)}
.dots{display:flex;gap:12px;align-items:center}
.dots span{width:5px;height:5px;border-radius:50%;background:var(--white)}
.dots span.on{width:11px;height:11px;background:var(--orange)}
.dots.dark span{background:var(--text)}
.dots.dark span.on{background:var(--orange)}

/* section headings */
.sec-rule{width:170px;height:2px;background:var(--orange);left:515px}
.sec-title{left:0;width:1200px;text-align:center;font-family:"Poppins",sans-serif;font-weight:800;font-size:40px;letter-spacing:2px;color:var(--text)}
.sec-sub{left:0;width:1200px;text-align:center;font-size:13px;font-weight:600;letter-spacing:1px}

.about-copy{top:826px;left:118px;width:964px;text-align:center;font-size:14px;line-height:26px;color:var(--muted);letter-spacing:.3px}
.feature{width:240px;text-align:center}
.feature .icon{width:52px;height:52px;margin:0 auto 18px;border-radius:10px;background:linear-gradient(135deg,#f5a25a,#e2533a 55%,#3f5b8c)}
.feature p{font-size:14px;font-weight:600;letter-spacing:1.2px;line-height:23px;text-transform:uppercase}

/* services */
.card{top:1305px;width:313px;height:255px;background:var(--white);box-shadow:0 1px 6px rgba(0,0,0,.12)}
.card .img{height:207px}
.card .label{height:48px;display:flex;align-items:center;justify-content:center;font-size:13px;letter-spacing:.3px;text-transform:uppercase}
.img-remodel{background:linear-gradient(160deg,#e9e6e2,#d7c4a8 60%,#c0914f)}
.img-garden{background:linear-gradient(170deg,#6d6f4f,#5b8a3a 45%,#b57db2 70%,#4f9b2c)}
.img-building{background:linear-gradient(180deg,#7fb1e0,#3f86c9 50%,#a9c1cf 80%,#5f8a4e)}

/* stats */
.stats{left:0;top:1699px;width:1200px;height:401px;background:linear-gradient(180deg,#2a3f86 0%,#3a58a1 40%,#5a6a88 65%,#4b3d3a 100%)}
.stat{width:260px;text-align:center}
.stat .num{font-family:"Poppins",sans-serif;font-weight:700;font-size:58px;color:var(--orange);line-height:60px}
.stat .cap{margin-top:18px;font-size:21px;font-weight:600;color:var(--white);letter-spacing:1px}

/* contact */
.form-card{left:243px;top:2275px;width:791px;height:400px;background:var(--white);box-shadow:0 2px 14px rgba(0,0,0,.08)}
.info-panel{left:180px;top:2307px;width:329px;height:335px;background:var(--navy);color:var(--white)}
.info-panel h3{position:absolute;left:36px;top:30px;font-size:27px;font-weight:600;color:var(--orange)}
.info-row{position:absolute;left:36px;display:flex;gap:22px;font-size:14px;line-height:20px;font-weight:300}
.info-row svg{flex:none;margin-top:2px}
.field{background:var(--field);font-size:12px;color:#666;padding:13px 11px}
.submit{left:525px;top:2728px;width:150px;height:44px;background:var(--orange);color:var(--white);font-size:13px;font-weight:600;display:flex;align-items:center;justify-content:center;letter-spacing:.5px}

/* footer */
.footer{left:0;top:2860px;width:1200px;height:400px;background:var(--footer);color:var(--white)}
.footer .about{position:absolute;left:111px;top:156px;width:300px;font-size:13px;line-height:21.5px;font-weight:300}
.footer h4{position:absolute;top:82px;font-size:15px;font-weight:600;letter-spacing:.5px}
.footer ul{position:absolute;list-style:none;font-size:13px;line-height:26px;font-weight:300}
.footer .socials{position:absolute;left:939px;top:242px;display:flex;gap:12px}
.footer .socials span{width:18px;height:18px;border-radius:50%;border:1.5px solid var(--white)}
.footer .license{position:absolute;left:939px;top:294px;font-size:13px}
.footer .copy{position:absolute;left:0;width:1200px;top:352px;text-align:center;font-size:11px;font-weight:300}
</style>
</head>
<body>

<!-- HERO -->
<section class="abs hero" role="img" aria-label="Photo of construction workers in hard hats looking up at high-rise buildings under construction"></section>
<div class="abs brand" style="left:111px;top:38px"><span class="mark"></span><span class="words"><span>SUMMIT</span><span>BUILDERS</span></span></div>
<nav class="abs nav">
  <a class="active" style="left:337px">HOME</a>
  <a style="left:419px">ABOUT US</a>
  <a style="left:538px">SERVICES</a>
  <a style="left:653px">PROJECTS</a>
  <a style="left:772px">CONTACT US</a>
</nav>
<div class="abs quote-btn">GET A QUOTE</div>
<svg class="abs side-social" style="left:50px;top:278px" width="12" height="86" aria-label="Social links">
  <circle cx="6" cy="6" r="5"/><circle cx="6" cy="44" r="5"/><circle cx="6" cy="80" r="5"/>
</svg>
<h1 class="abs hero-title">THE BEST CHOOSE US</h1>
<p class="abs hero-sub">Because We Deliver</p>
<div class="abs dots" style="left:571px;top:592px"><span class="on"></span><span></span><span></span><span></span></div>

<!-- ABOUT -->
<div class="abs sec-rule" style="top:710px"></div>
<h2 class="abs sec-title" style="top:714px">ABOUT US</h2>
<p class="abs sec-sub" style="top:771px">WE DELIVER LANDMARK PROJECTS</p>
<p class="abs about-copy">We are rethoric question ran over her cheek When she reached the first hills of the Italic Mountains, she had a last view back on the skyline of her hometown Bookmarksgrove, the headline of Alphabet Village and the subline of her own road, the Line Lane.</p>
<div class="abs feature" style="left:96px;top:932px"><div class="icon" role="img" aria-label="Icon of a hand holding a star"></div><p>We've repution<br>for excellence</p></div>
<div class="abs feature" style="left:362px;top:932px"><div class="icon" role="img" aria-label="Icon of connected partners network"></div><p>We build<br>partnerships</p></div>
<div class="abs feature" style="left:617px;top:932px"><div class="icon" role="img" aria-label="Icon of a person beside a checklist"></div><p>Guided by<br>commitment</p></div>
<div class="abs feature" style="left:876px;top:932px"><div class="icon" role="img" aria-label="Icon of a team of three people"></div><p>A team of<br>professionals</p></div>

<!-- WHAT WE DO -->
<div class="abs sec-rule" style="top:1198px"></div>
<h2 class="abs sec-title" style="top:1204px">WHAT WE DO</h2>
<div class="abs card" style="left:111px"><div class="img img-remodel" role="img" aria-label="Photo of a bright room under renovation"></div><div class="label">Residential Remodels</div></div>
<div class="abs card" style="left:443px"><div class="img img-garden" role="img" aria-label="Photo of a landscaped garden with flower beds"></div><div class="label">Landscaping</div></div>
<div class="abs card" style="left:775px"><div class="img img-building" role="img" aria-label="Photo of a modern glass office building"></div><div class="label">Building ADU (Accessory Dwelling Unit)</div></div>
<div class="abs dots dark" style="left:571px;top:1603px"><span class="on"></span><span></span><span></span><span></span></div>

<!-- STATS -->
<section class="abs stats" role="img" aria-label="Photo of a suburban house roof against a blue sky"></section>
<div class="abs stat" style="left:89px;top:1847px"><div class="num">53</div><div class="cap">TOTAL PROJECTS</div></div>
<div class="abs stat" style="left:346px;top:1847px"><div class="num">371</div><div class="cap">STAFF MEMBERS</div></div>
<div class="abs stat" style="left:600px;top:1847px"><div class="num">15</div><div class="cap">WORKING IN STATES</div></div>
<div class="abs stat" style="left:864px;top:1847px"><div class="num">2,600</div><div class="cap">HOURS FOR WORK</div></div>

<!-- CONTACT -->
<div class="abs sec-rule" style="top:2163px"></div>
<h2 class="abs sec-title" style="top:2170px">CONTACT US</h2>
<div class="abs form-card"></div>
<div class="abs info-panel">
  <h3>Contact</h3>
  <div class="info-row" style="top:96px">
    <svg width="12" height="15" viewBox="0 0 12 15"><path d="M6 0a6 6 0 0 0-6 6c0 4 6 9 6 9s6-5 6-9a6 6 0 0 0-6-6z" fill="var(--orange)"/><circle cx="6" cy="6" r="2.2" fill="var(--navy)"/></svg>
    <span>412 W Orchard Ridge Ave Larkfield,<br>CA 90210</span></div>
  <div class="info-row" style="top:166px">
    <svg width="12" height="12" viewBox="0 0 12 12"><path d="M2 0l2.5 2.8-1.2 1.6a8 8 0 0 0 4.3 4.3l1.6-1.2L12 10l-1.7 2C5 12 0 7 0 1.7z" fill="var(--orange)"/></svg>
    <span>+1 555 308 2714</span></div>
  <div class="info-row" style="top:215px">
    <svg width="15" height="11" viewBox="0 0 15 11"><rect x=".6" y=".6" width="13.8" height="9.8" fill="none" stroke="var(--orange)" stroke-width="1.2"/><path d="M.6.6l6.9 5.5L14.4.6" fill="none" stroke="var(--orange)" stroke-width="1.2"/></svg>
    <span>hello@summitbuildersca.example</span></div>
  <div class="info-row" style="top:269px">
    <svg width="13" height="15" viewBox="0 0 13 15"><circle cx="6.5" cy="6.5" r="5.5" fill="none" stroke="var(--orange)" stroke-width="1.4"/></svg>
    <span>ISO 9001:2017</span></div>
</div>
<div class="abs field" style="left:541px;top:2307px;width:210px;height:41px">First Name</div>
<div class="abs field" style="left:772px;top:2307px;width:212px;height:41px">Last Name</div>
<div class="abs field" style="left:541px;top:2372px;width:443px;height:42px">Email</div>
<div class="abs field" style="left:541px;top:2440px;width:443px;height:41px">Phone</div>
<div class="abs field" style="left:541px;top:2505px;width:443px;height:137px">Message</div>
<div class="abs submit">SUBMIT</div>

<!-- FOOTER -->
<footer class="abs footer">
  <div class="brand" style="position:absolute;left:111px;top:92px"><span class="mark"></span><span class="words"><span>SUMMIT</span><span>BUILDERS</span></span></div>
  <p class="about">We are rethoric question ran over her cheek When she reached the first hills of the Italic Mountains, she had a last view back on the skyline of her hometown Bookmarksgrove, the headline of Alphabet Village and the subline of her own road, the Line Lane.</p>
  <h4 style="left:498px">QUICK LINKS</h4>
  <ul style="left:498px;top:146px"><li>Home</li><li>About us</li><li>Services</li><li>Projects</li><li>Contact us</li></ul>
  <h4 style="left:675px">TIMING</h4>
  <ul style="left:675px;top:146px"><li>Monday – Friday: 10:00 – 16:00</li><li>Saturday: 12:00 – 15:00</li><li>Sunday and Holidays: 09:00 – 12:00</li></ul>
  <h4 style="left:939px">CONTACT US</h4>
  <ul style="left:939px;top:146px;line-height:21.5px"><li>412 W Orchard Ridge Ave</li><li>Larkfield,</li><li>CA 90210</li></ul>
  <div class="socials" aria-label="Social links"><span></span><span></span><span></span><span></span><span></span></div>
  <p class="license">CSLB License # 2418596</p>
  <p class="copy">Copyright © 2020 Summit Builders</p>
</footer>

</body>
</html>
```